Design a modern, classy & professional business card for an online real estate agency, specializing in medium-luxury properties in Thailand and later in Singapore and UK.

Possible design ideas so far: (not essential)

- curved corner(s) to the card, white on front & turquoise on back or visa versa.

- front of card - clear and simple, company name in metallic grey/monochrome, logo graphic & company name on front in spot UV or embossed/debossed effect.

- back of card - large, close-cropped, 'ghost' patterns of the C-shaped curves of logo, or company name repeated on back of card in spot UV.

Target Market(s)

- young to middle-aged professionals mainly (but ideally should design should suit all)

- UK, US,EU,AUS & ASIAN mainly (but ideally should design should suit all countries)

Industry/Entity Type

Real Estate

Requirements
Must have
• THEME:
- Luxurious & Modern
- Clean & striking
- Unique & creative

INFO:
- Logo & company name on front
- Contact details on back:

Tobias Hennlund
Managing Director

www.velmontestates.asia
www.velmontestates.co.uk

Tel: 083-274-6159
email: tobias@velmontestates.asia

(contact details can be displayed in any order as suites design.)

Nice to have
• - curved corner(s) to the card, white on front & turquoise on back or visa versa.

Should not have
• - No generic images of properties, palm trees/coconut trees etc.

- No other other bold colors, except for main turquoise, grey, metallic white & black theme.

- No obvious business card templates

```html
<!DOCTYPE html>
<html lang="en">
<head>
<meta charset="utf-8">
<title>Velmont Estates – Business Card</title>
<link rel="stylesheet" href="https://fonts.googleapis.com/css2?family=Exo+2:wght@400;500&display=swap">
<style>
  :root {
    --canvas: #ecebe8;
    --card: #ffffff;
    --card-shade: #ececec;
    --turquoise: #22c6c4;
    --grey: #8a8a8a;
    --grey-dark: #5f5f5f;
    --ink: #2b2b2b;
    --black: #1c1c1c;
    --band-top: #3a3a3a;
    --pale-top: #f2f2f2;
    --pale-bottom: #d6d6d6;
    --white: #ffffff;
  }
  * { box-sizing: border-box; margin: 0; padding: 0; }
  html, body { width: 1057px; height: 1200px; overflow: hidden; }
  body {
    background: var(--canvas);
    font-family: "Exo 2", "Helvetica Neue", Arial, sans-serif;
    color: var(--ink);
  }
  .sheet {
    width: 1057px; height: 1200px;
    display: flex; justify-content: center; align-items: center; gap: 64px;
  }
  .card {
    position: relative;
    width: 440px; height: 770px;
    background: linear-gradient(160deg, var(--card) 55%, var(--card-shade) 100%);
    border-radius: 4px;
    box-shadow: 0 14px 36px rgba(0,0,0,0.16);
    overflow: hidden;
  }

  /* brand name with one plain square */
  .brand {
    position: absolute;
    display: flex; align-items: center;
    color: var(--grey);
    font-family: "Exo 2", Arial, sans-serif;
    font-weight: 500;
    white-space: nowrap;
  }
  .brand-square { background: var(--turquoise); flex: none; }
  .card--back .brand { top: 80px; right: 42px; gap: 12px; font-size: 28px; }
  .card--back .brand-square { width: 26px; height: 26px; }
  .card--front .brand { top: 250px; left: 0; right: 0; justify-content: center; gap: 16px; font-size: 40px; }
  .card--front .brand-square { width: 38px; height: 38px; }

  /* contact list */
  .contacts {
    position: absolute; top: 250px; left: 46px;
    list-style: none;
    font-size: 17px; color: var(--grey-dark);
  }
  .contacts li { display: flex; align-items: center; gap: 12px; margin-bottom: 16px; }
  .contacts .address { display: block; line-height: 1.4; margin-bottom: 18px; font-size: 18px; }
  .icon {
    width: 24px; height: 24px; flex: none;
    background: var(--turquoise); border-radius: 4px;
    display: flex; align-items: center; justify-content: center;
  }
  .icon svg { width: 15px; height: 15px; }

  /* bottom band */
  .band { position: absolute; left: 0; right: 0; bottom: 0; height: 220px; }
  .band--dark { background: linear-gradient(180deg, var(--band-top) 0%, var(--black) 45%); }
  .band--pale { background: linear-gradient(160deg, var(--pale-top) 0%, var(--pale-bottom) 100%); }

  .holder {
    position: absolute; right: 36px; bottom: 44px;
    text-align: right; color: var(--white);
    font-weight: 500;
  }
  .holder-name { font-size: 30px; letter-spacing: 3px; text-transform: uppercase; }
  .holder-role { font-size: 19px; letter-spacing: 3px; text-transform: uppercase; margin-top: 6px; }
  .front-web {
    position: absolute; left: 60px; bottom: 78px;
    font-size: 17px; color: var(--ink); letter-spacing: 0.5px;
  }
</style>
</head>
<body>
<main class="sheet">

  <!-- contact side -->
  <section class="card card--back" aria-label="Card contact side">
    <div class="brand">
      <span class="brand-square"></span>
      <span class="brand-name">Velmont Estates</span>
    </div>

    <ul class="contacts">
      <li class="address">42 Rama Lane,<br>Tower B, 3rd Floor</li>
      <li>
        <span class="icon"><svg viewBox="0 0 16 16"><path fill="#fff" d="M3.5 1.5l2.5 0 1 3.5-1.6 1.2a8 8 0 0 0 4.4 4.4L11 9l3.5 1v2.5c0 .8-.7 1.5-1.5 1.5A11 11 0 0 1 2 3c0-.8.7-1.5 1.5-1.5z"/></svg></span>
        Tel: 083-274-6159
      </li>
      <li>
        <span class="icon"><svg viewBox="0 0 16 16"><rect x="2" y="4" width="12" height="8" rx="1" fill="none" stroke="#fff" stroke-width="1.5"/><path d="M2.5 4.5L8 9l5.5-4.5" fill="none" stroke="#fff" stroke-width="1.5"/></svg></span>
        tobias@velmontestates.asia
      </li>
      <li>
        <span class="icon"><svg viewBox="0 0 16 16"><circle cx="8" cy="8" r="6" fill="none" stroke="#fff" stroke-width="1.4"/><ellipse cx="8" cy="8" rx="2.6" ry="6" fill="none" stroke="#fff" stroke-width="1.2"/><path d="M2 8h12" stroke="#fff" stroke-width="1.2"/></svg></span>
        www.velmontestates.asia
      </li>
      <li>
        <span class="icon"><svg viewBox="0 0 16 16"><circle cx="8" cy="8" r="6" fill="none" stroke="#fff" stroke-width="1.4"/><ellipse cx="8" cy="8" rx="2.6" ry="6" fill="none" stroke="#fff" stroke-width="1.2"/><path d="M2 8h12" stroke="#fff" stroke-width="1.2"/></svg></span>
        www.velmontestates.co.uk
      </li>
    </ul>

    <div class="band band--dark" role="img" aria-label="Decorative curved band in grey, turquoise and black"></div>
    <div class="holder">
      <div class="holder-name">Tobias Hennlund</div>
      <div class="holder-role">Managing Director</div>
    </div>
  </section>

  <!-- logo side -->
  <section class="card card--front" aria-label="Card logo side">
    <div class="brand">
      <span class="brand-square"></span>
      <span class="brand-name">Velmont Estates</span>
    </div>

    <div class="band band--pale" role="img" aria-label="Decorative curved band in grey, turquoise and pale silver"></div>
    <div class="front-web">www.velmontestates.asia</div>
  </section>

</main>
</body>
</html>
```